Copperwell Lottery Landing Page -

We are looking for a unique Landing Page design that makes users want to subscribe!
Banner artwork, copperwell promo video (already created), subscription info, product highlights. Why users would want to subscribe.
The initial work was done in PHP. I will provide the website in it's current state in a zip file. The website can be run locally with XAMPP.
Target Market(s)
Anyone who plays the lottery and wants to win more!
Industry/Entity Type
Lottery, USA and Canada (More Countries will be added soon)
Coding
Coded - Design and coding required
Other font styles liked:
- Unzip the the work we have currently done and this should give you a good idea of what direction we are going. We love this theme but now we just need to
Requirements
Must have
- After you unzip the copperwell.zip and open the site using XAMPP

```html
<!DOCTYPE html>
<html lang="en">
<head>
<meta charset="utf-8">
<title>Copperwell Lottery Software</title>
<link href="https://fonts.googleapis.com/css2?family=Oswald:wght@400;500;600&family=Mulish:wght@400;600&display=swap" rel="stylesheet">
<style>
:root{
  --red:#f23a3c;
  --dark:#111111;
  --text:#333333;
  --light:#f4f3f4;
  --grey-card:#e6e6e8;
  --footer:#1e1e1e;
  --white:#ffffff;
}
*{margin:0;padding:0;box-sizing:border-box}
html,body{width:1200px;height:3147px;overflow:hidden}
body{font-family:'Mulish',sans-serif;color:var(--text);background:var(--white);position:relative}
.head{font-family:'Oswald',sans-serif;font-weight:500;text-transform:uppercase}
section,header,footer{position:absolute;left:0;width:1200px}
.abs{position:absolute}
.btn{display:inline-block;background:var(--red);color:var(--white);font-family:'Oswald',sans-serif;font-weight:500;text-transform:uppercase;text-align:center}
/* header */
.site-header{top:0;height:106px;background:var(--white)}
.brand{left:132px;top:26px;display:flex;align-items:center;gap:10px;font-family:'Oswald',sans-serif;font-weight:600;font-size:28px;color:var(--red);line-height:1}
.brand-dot{width:46px;height:46px;border-radius:50%;background:var(--red)}
.brand small{display:block;font-size:15px;font-weight:600;color:var(--red)}
.top-btns{right:132px;top:19px;display:flex;gap:16px}
.btn-outline{border:2px solid var(--red);color:var(--red);background:var(--white);font-family:'Oswald',sans-serif;font-size:17px;padding:4px 14px;text-transform:uppercase}
.top-btns .btn{font-size:17px;padding:6px 14px}
.nav{right:132px;top:69px;display:flex;gap:33px;font-family:'Oswald',sans-serif;font-size:17px;color:var(--dark);text-transform:uppercase}
.nav .on{color:var(--red)}
/* hero */
.hero{top:106px;height:575px;background:linear-gradient(90deg,#2a0b3a 0%,#4a1558 40%,#3a0f40 70%,#1c0820 100%)}
.hero-art{left:80px;top:60px;width:560px;height:470px;border-radius:40% 40% 8px 8px;background:radial-gradient(circle at 50% 45%,#8a2a70 0%,#5a1a5e 45%,rgba(60,16,70,0) 72%)}
.hero-title{left:733px;top:146px;font-size:48px;line-height:58px;color:var(--red);white-space:nowrap}
.hero .btn{left:742px;top:346px;font-size:21px;padding:6px 16px}
.dots{left:568px;top:532px;display:flex;gap:8px}
.dots i{width:11px;height:11px;border-radius:50%;border:2px solid var(--white)}
.dots i.on{background:var(--red)}
/* section titles */
.sec-title{width:1200px;text-align:center;font-size:31px;color:var(--dark)}
.sec-title span{color:var(--red)}
.rule{left:587px;width:26px;height:3px;background:var(--dark)}
/* video */
.video{top:681px;height:630px;background:linear-gradient(135deg,#f7f7f7,#ececec 50%,#f7f7f7)}
.video-frame{left:133px;top:117px;width:930px;height:472px;background:radial-gradient(circle at 50% 45%,#c02e3e 0%,#7a1422 50%,#2a0408 100%)}
.play{left:570px;top:195px;width:56px;height:56px;border-radius:50%;background:var(--red);display:flex;align-items:center;justify-content:center}
/* products */
.products{top:1311px;height:518px;background:var(--light)}
.prod{top:127px;width:226px;text-align:center}
.prod-img{width:226px;height:195px;background:linear-gradient(180deg,#3c4a3a 0%,#7a5a30 50%,#3a2a1a 100%)}
.prod h3{margin-top:20px;font-size:17px;color:var(--red)}
.prod p{margin:14px auto 0;width:190px;font-size:12.5px;line-height:17.5px;color:var(--text)}
.prod .btn{margin-top:12px;font-size:11px;padding:3px 10px}
/* subscription */
.subs{top:1829px;height:660px;background:#fbf7f7}
.card{background:var(--white);text-align:center;box-shadow:0 4px 14px rgba(0,0,0,.08)}
.card-top{background:var(--grey-card);padding-top:32px;height:161px}
.card h4{font-size:19px;color:var(--dark)}
.price{margin-top:6px;font-family:'Oswald',sans-serif;font-size:27px;color:var(--red)}
.price small{font-family:'Mulish',sans-serif;font-size:12px;color:var(--text)}
.card-top p{margin:8px auto 0;width:200px;font-size:12.5px;line-height:17.5px}
.card ul{list-style:none;width:220px;margin:20px auto 0}
.card li{font-size:12.5px;padding:6px 0 6px;border-bottom:1px solid #e2e2e2}
.card li:last-child{border-bottom:none}
.card .btn{margin-top:20px;font-size:16px;padding:3px 14px}
.card.featured .card-top{background:var(--red);height:198px;padding-top:42px}
.card.featured h4,.card.featured .price,.card.featured .price small,.card.featured .card-top p{color:var(--white)}
/* why */
.why{top:2489px;height:432px;background:linear-gradient(135deg,#eeeeee,#f6f6f6 50%,#e9e9e9)}
.why-img{left:130px;top:46px;width:461px;height:340px;background:linear-gradient(160deg,#5a3a22 0%,#8a5a30 40%,#1d5a48 100%)}
.why h2{left:639px;top:46px;font-size:30px;line-height:37px;color:var(--dark)}
.why .rule{left:639px;top:126px}
.why-copy{left:639px;top:158px;width:420px;font-size:14.5px;line-height:21px}
.why ul{left:639px;top:260px;list-style:none;font-size:14.5px}
.why li{height:28px;display:flex;align-items:center;gap:10px}
.why li svg{flex:none}
/* footer */
.site-footer{top:2921px;height:226px;background:var(--footer)}
.site-footer .brand{top:44px;font-size:36px}
.site-footer .brand-dot{width:52px;height:52px}
.site-footer .brand small{font-size:19px}
.follow{right:132px;top:52px;display:flex;align-items:center;gap:20px;font-family:'Oswald',sans-serif;font-size:14px;color:var(--white)}
.follow i{width:24px;height:24px;border-radius:50%;background:var(--white)}
.fnav{right:132px;top:112px;display:flex;gap:28px;font-family:'Oswald',sans-serif;font-size:17px;color:var(--white);text-transform:uppercase}
.fline{left:132px;top:156px;width:936px;height:1px;background:#3c3c3c}
.copy{top:187px;width:1200px;text-align:center;font-size:12px;color:var(--white)}
</style>
</head>
<body>

<header class="site-header">
  <div class="abs brand"><span class="brand-dot"></span><div>Copperwell<small>Lottery Software</small></div></div>
  <div class="abs top-btns"><span class="btn-outline">Join and Login</span><span class="btn">Subscribe</span></div>
  <nav class="abs nav"><span class="on">Home</span><span>About Us</span><span>Product</span><span>Services</span><span>Blog</span><span>Contact Us</span></nav>
</header>

<section class="hero">
  <div class="abs hero-art" role="img" aria-label="Casino illustration with playing cards, roulette wheel, 777 slot machine, dice and flying chips on a glowing stage"></div>
  <h1 class="abs head hero-title">Welcome to<br>Copperwell Lottery<br>Software</h1>
  <span class="abs btn">Read More</span>
  <div class="abs dots"><i></i><i class="on"></i><i></i><i></i></div>
</section>

<section class="video">
  <h2 class="abs head sec-title" style="top:36px">Our <span>Video</span></h2>
  <div class="abs rule" style="top:85px"></div>
  <div class="abs video-frame" role="img" aria-label="Promo video cover with lottery tickets, lottery balls and gold coins on a red burst background">
    <div class="abs play"><svg width="22" height="24" viewBox="0 0 22 24"><path d="M2 1 L21 12 L2 23 Z" fill="#fff"/></svg></div>
  </div>
</section>

<section class="products">
  <h2 class="abs head sec-title" style="top:38px">Our <span>Products</span></h2>
  <div class="abs rule" style="top:86px"></div>
  <div class="abs prod" style="left:131px"><div class="prod-img" role="img" aria-label="Roulette wheel close-up"></div><h3 class="head">Product 1</h3><p>Lorem Ipsum is simply dummy text of the printing and types etting industry</p><span class="btn">Read More</span></div>
  <div class="abs prod" style="left:367px"><div class="prod-img" role="img" aria-label="Roulette wheel close-up"></div><h3 class="head">Product 2</h3><p>Lorem Ipsum is simply dummy text of the printing and types etting industry</p><span class="btn">Read More</span></div>
  <div class="abs prod" style="left:605px"><div class="prod-img" role="img" aria-label="Roulette wheel close-up"></div><h3 class="head">Product 3</h3><p>Lorem Ipsum is simply dummy text of the printing and types etting industry</p><span class="btn">Read More</span></div>
  <div class="abs prod" style="left:841px"><div class="prod-img" role="img" aria-label="Roulette wheel close-up"></div><h3 class="head">Product 4</h3><p>Lorem Ipsum is simply dummy text of the printing and types etting industry</p><span class="btn">Read More</span></div>
</section>

<section class="subs">
  <h2 class="abs head sec-title" style="top:43px">Subscription</h2>
  <div class="abs rule" style="top:99px"></div>
  <div class="abs card" style="left:131px;top:173px;width:312px;height:404px">
    <div class="card-top"><h4 class="head">Lorem Ipsum</h4><div class="price">$15.99 <small>/ month</small></div><p>Lorem Ipsum is simply dummy text of the printing and</p></div>
    <ul><li>There are many variations</li><li>It is a long established fact</li><li>Contrary to popular belie Lorem</li><li>Lorem Ipsum is simply dummy</li><li>It is a long established fact</li></ul>
    <span class="btn">Subscribe</span>
  </div>
  <div class="abs card" style="left:757px;top:173px;width:312px;height:404px">
    <div class="card-top"><h4 class="head">Lorem Ipsum</h4><div class="price">$35.99 <small>/ month</small></div><p>Lorem Ipsum is simply dummy text of the printing and</p></div>
    <ul><li>There are many variations</li><li>It is a long established fact</li><li>Contrary to popular belie Lorem</li><li>Lorem Ipsum is simply dummy</li><li>It is a long established fact</li></ul>
    <span class="btn">Subscribe</span>
  </div>
  <div class="abs card featured" style="left:443px;top:136px;width:313px;height:473px">
    <div class="card-top"><h4 class="head">Lorem Ipsum</h4><div class="price">$25.99 <small>/ month</small></div><p>Lorem Ipsum is simply dummy text of the printing and</p></div>
    <ul><li>There are many variations</li><li>It is a long established fact</li><li>Contrary to popular belie Lorem</li><li>Lorem Ipsum is simply dummy</li><li>It is a long established fact</li></ul>
    <span class="btn">Subscribe</span>
  </div>
</section>

<section class="why">
  <div class="abs why-img" role="img" aria-label="Silver 777 slot machine surrounded by stacks of casino chips, cards and dice"></div>
  <h2 class="abs head">Why users would<br>want to subscribe?</h2>
  <div class="abs rule"></div>
  <p class="abs why-copy">There are many variations of passages of Lorem Ipsum avail able, but the majority have suffered alteration in some form, by injected humour, or randomised words which don't look even slightly believable.</p>
  <ul class="abs">
    <li><svg width="6" height="9" viewBox="0 0 6 9"><path d="M0 0 L6 4.5 L0 9 Z" fill="#f23a3c"/></svg>Lorem Ipsum is simply dummy text of the</li>
    <li><svg width="6" height="9" viewBox="0 0 6 9"><path d="M0 0 L6 4.5 L0 9 Z" fill="#f23a3c"/></svg>It is a long established fact that a reader</li>
    <li><svg width="6" height="9" viewBox="0 0 6 9"><path d="M0 0 L6 4.5 L0 9 Z" fill="#f23a3c"/></svg>There are many variations of passage</li>
    <li><svg width="6" height="9" viewBox="0 0 6 9"><path d="M0 0 L6 4.5 L0 9 Z" fill="#f23a3c"/></svg>Sed ut perspiciatis unde omnis iste natus error</li>
    <li><svg width="6" height="9" viewBox="0 0 6 9"><path d="M0 0 L6 4.5 L0 9 Z" fill="#f23a3c"/></svg>But I must explain to you how all this</li>
  </ul>
</section>

<footer class="site-footer">
  <div class="abs brand"><span class="brand-dot"></span><div>Copperwell<small>Lottery Software</small></div></div>
  <div class="abs follow"><span>FOLLOW US</span><i></i><i></i><i></i><i></i></div>
  <nav class="abs fnav"><span>Home</span><span>About Us</span><span>Product</span><span>Services</span><span>Blog</span><span>Contact Us</span></nav>
  <div class="abs fline"></div>
  <p class="abs copy">Copyright © 2022 All Rights Reserved</p>
</footer>

</body>
</html>
```